Card design for orthopaedic surgeons working as The Brightwater Joint Centre

Business cards, letterhead

Colors

Designer to choose colors to be used in the design.

Requirements
Must have
• Late addition.
• Cards letterhead must have logos of
• Crestmoor Lindell College of Surgeons
• Varenwood Bone Health Association
Nice to have
• Back of card to have space for appointment time to be added by hand and some blank space for writing incidental other notes.

```html
<!DOCTYPE html>
<html lang="en">
<head>
<meta charset="UTF-8">
<title>The Brightwater Joint Centre – Business Card</title>
<link rel="stylesheet" href="https://fonts.googleapis.com/css2?family=Lato:wght@400;700&display=swap">
<style>
  :root {
    --backdrop: #2b2b2d;
    --card: #141415;
    --card-edge: #1e1e20;
    --accent: #29a3e8;
    --accent-deep: #0d4f7a;
    --text-light: #dcdcdc;
    --text-muted: #c4c4c4;
    --divider: #6a6a6a;
  }
  * { box-sizing: border-box; margin: 0; padding: 0; }
  html, body {
    width: 1200px; height: 900px; overflow: hidden;
    background: var(--backdrop);
    font-family: "Lato", sans-serif;
  }
  .stage {
    width: 1200px; height: 900px;
    display: flex; flex-direction: column;
    align-items: center; justify-content: center; gap: 48px;
  }
  .card {
    position: relative;
    width: 600px; height: 343px;
    background: linear-gradient(160deg, var(--card-edge), var(--card));
    box-shadow: 0 10px 30px rgba(0,0,0,.45);
    overflow: hidden;
  }
  .card__band {
    position: absolute; left: 0; right: 0; bottom: 0; height: 9px;
    background: linear-gradient(90deg, var(--accent-deep), var(--accent) 50%, var(--accent-deep));
  }
  /* Front */
  .card--front { display: flex; align-items: center; justify-content: center; }
  .brand {
    display: flex; align-items: center; gap: 12px;
    margin-top: -10px;
    color: var(--accent);
    font-weight: 400; font-size: 26px; letter-spacing: .2px;
    white-space: nowrap;
  }
  .brand__dot {
    width: 12px; height: 12px; border-radius: 50%;
    background: var(--accent);
  }
  /* Back */
  .identity-row {
    position: absolute; top: 150px; left: 40px; right: 40px;
    display: flex; align-items: flex-start;
  }
  .person { width: 258px; text-align: right; padding-right: 26px; }
  .person__name {
    color: var(--accent); font-weight: 700; font-size: 23px;
    letter-spacing: .5px; text-transform: uppercase; white-space: nowrap;
  }
  .person__role { color: var(--text-light); font-size: 16px; margin-top: 2px; }
  .divider { width: 1px; height: 64px; background: var(--divider); margin-top: 8px; }
  .contacts { list-style: none; padding-left: 22px; margin-top: 14px; }
  .contacts li {
    display: flex; align-items: center; gap: 8px;
    color: var(--text-light); font-size: 16px; line-height: 22px;
    white-space: nowrap;
  }
  .contacts svg { width: 12px; height: 12px; fill: var(--accent); flex: none; }
  .address {
    position: absolute; left: 0; right: 0; top: 262px;
    text-align: center; color: var(--text-muted); font-size: 16px;
  }
</style>
</head>
<body>
<main class="stage">
  <section class="card card--front">
    <div class="brand">
      <span class="brand__dot"></span>
      <span class="brand__name">The Brightwater Joint Centre</span>
    </div>
    <div class="card__band"></div>
  </section>

  <section class="card card--back">
    <div class="identity-row">
      <div class="person">
        <p class="person__name">Daniel Marsh</p>
        <p class="person__role">Managing Director</p>
      </div>
      <div class="divider"></div>
      <ul class="contacts">
        <li>
          <svg viewBox="0 0 12 12" aria-hidden="true"><path d="M1 4c0-2 2-3 5-3s5 1 5 3l-2 1-1-1.5H4L3 5 1 4zm2 2h6l1 5H2l1-5zm3 1a1.5 1.5 0 1 0 0 3a1.5 1.5 0 0 0 0-3z"/></svg>
          044-987 654 321
        </li>
        <li>
          <svg viewBox="0 0 12 12" aria-hidden="true"><path d="M0 2h12v8H0zM1 3v.4l5 3.3 5-3.3V3z"/></svg>
          hello@brightwaterjoint.com
        </li>
        <li>
          <svg viewBox="0 0 12 12" aria-hidden="true"><circle cx="6" cy="6" r="5.5"/></svg>
          www.brightwaterjoint.com
        </li>
      </ul>
    </div>
    <p class="address">421, Address line here, 45452,Country Name</p>
    <div class="card__band"></div>
  </section>
</main>
</body>
</html>
```